Superfood Organic Powder needs a new Standup Pouch Design

Superfood brand needs a new package design Standup pouch

We need a new packaging design
*Standup Pouch*
for a NEW superfood product to our brand PureLeafy.

This product is a superfood blend of organic powders such as spiralina, chlorella, wheatgrass etc.

The design should be modern with an organic look, - but feel free to play around with it as you wish.

Our first or *older* product is called Vital Blendo, and contains superfood powders like Maca, Moringa, Baobab, Spirulina, Chlorella, Wheatgrass

Find measurements for the standup pouch in the attachments.

We can either go with a

a white standup pouch with a slight opacity to it
(see attached sample I have from my supplier)

or

mat white standup pouch

Or Natural Kraft if

The white pouch with a slight opacity to it so you can see the powder through the pouch. One cool thing about this one is that if we have an area in the design with no colors, not even white, that area will be completely transparent, see picture of the sample pouch we have in the attachments.
In the sample photo the spider is completely transparent.

The Mat white pouch is just a basic white standup pouch with a mat finish.
What ever you think is best for your design you can suggest.

In the future we will create multiple products, each product should have its own color style to distinguish between them - this product should use green Color code as one of the green colors used in the logo. Of course not all colors should have that code, but just the identifier for this product. Please present an idea to showcase this identifier, it could be a thick horizontal or vertical line somewhere on the pouch.

The standup pouch will be digitally printed so we can use all areas of the pouch.

Please provide 3D mockup of the design in order to better get an idea of the design.
Remember that I consider you as the expert so I'm very open to any suggestions regarding this design - in the end the main goal is to attract customers and that is your area of expertise.

Please let me know if you have any questions - thanks in advance

I'm looking forward to working with you.

Here are some links I have found that I think is great designs just to give a little insight to my designs wishes.:

https://www.pinboardly.example/pin/100000000000000001/ https://www.verdanthusk.example/collections/all-superfood-products
https://www.pinboardly.example/pin/100000000000000002/
https://designduel.example/product-label-design/contests/print-design-stand-up-resealable-pouch-organic-spice-100003
https://www.pinboardly.example/pin/100000000000000004/
https://www.pinboardly.example/pin/10000000000000005/
https://www.pinboardly.example/pin/100000000000000006/
https://www.pinboardly.example/pin/100000000000000007/ https://www.pinboardly.example/pin/100000000000000008/
https://www.pinboardly.example/pin/10000000000000009/

Reason: Needed more work because I changed manufacturer of standup pouches.

Target Market(s)

Vegans, Organic interested clients, healthy living, Fitness, Juicers

Industry/Entity Type

Health And Wellness

Requirements
Must have
• The following text should be added on front of the label under the product name:
• Danish certified organic
• Superfood blend
• —
• The product contains the following ingredients and should be mentioned on the front - only the ingredients names:
• Maca, Moringa, Baobab, Spirulina, Chlorella, Wheatgrass
• —
• Organic logo:
• Organic EU logo should be present on the back (find logo in the attachments) To the right of the logo the following text is mandatory with Myriad Pro Regular as a type-font: See previous design for instructions.
• "EU-LOGO-HERE"
• DK-ØKO-000
• EU/ikke-EU-jordbrug
• EU/non-EU Agriculture
• Next to the EU organic logo we will place the danish organic logo which is attached as well, you can decide if it should be on the left or right side, it is a red Ø logo ( find in the attachments as well.
• —
• The label should contain a Nutritional Information with the danish language as primary. By law in Denmark the language used should be danish but it is allowed to add the English word after the danish separated by a /
• So it should be titled as Næringsindhold / Nutritional information (Title Bold font)
• And contain the following:
• energi (KJ/kcal)
• • fedt / fat (g)
• • - heraf mættede fedtsyrer / from saturated fat (g)
• • kulhydrat / carbohydrates (g)
• • - heraf sukkerarter / from sugar (g)
• • protein (g)
• • salt (g)
• • kostfibre / dietary fiber (g)
• —
• We need ingredients list on the back as well titled Ingredienser / Ingredients (Title Bold font)
• Maca, Moringa, Baobab, Spirulina, Chlorella, Hvedegræs / Wheatgrass
• Nettovægt / Netto weight 225 gr
• —-
• You can add some cool logos indicating that the product is:
• 100 % organic
• 100% vegan
• No additives
• Non-GMO
• Gluten free
• —
• Instructions (Title Bold font)
• Mix the superfood powder into 250 ml water with a twist of lemon, coconut water, green juice, smoothies, almond milk, or add to your favorit morning meal.
• Serving size 1-2 teaspoon
• Would be great with 3-4 images describing the instructions
• Image 1 could be fruit being put in a blender
• Image 2 could be 1 teaspoon with powder on top of a blender
• Image 3 could be a blender in use
• Image 4 poring the smoothie in to a glass to enjoy
• —
• Opbevaring / Storage (Title Bold font)
• Opbevares tørt og ikke for varmt
• Keep in a cool and dry place away from sunlight
• —
• Batch: (Title Bold font)
• Best before / Bedst før: (Title Bold font)
• —
• Barcode field
• Make room for a barcode
• —
• Produced in EU for: (Title Bold font)
• Kornvik IVS
• Tranebærvej 42
• 8960 Randers SØ
• Denmark
• www.pureleafy-shop.example (make this bold as well)
• —
• Follow us (Title Bold font)
• Instagram and facebook logo on the back with hashtag #pureleafyshop
• —
• Other than that pureleafy logo can be added as well, it is attached as well.
• I will attach our logo with original AI files.
• —
• Our mission (text)
• We want to provide our customers with the best possible superfood blends. Allowing our customers to get a product packed with antioxidants, vitamins and minerals to elevate their health to the next level. All our products are vegan friendly and GMO free - produced under the best possible circumstances.
• —
Nice to have
• Green color from the logo can be used to get it streamlined.
• Color code c2ce48

```html
<!DOCTYPE html>
<html lang="en">
<head>
<meta charset="utf-8">
<title>PureLeafy – Vital Blendo Standup Pouch</title>
<link href="https://fonts.googleapis.com/css2?family=Jost:wght@300;400;500&family=Kaushan+Script&display=swap" rel="stylesheet">
<style>
  :root {
    --bg: #e4e4e4;
    --pouch: #ffffff;
    --pouch-edge: #dcdcdc;
    --band-green: #45a241;
    --logo-green: #3fae49;
    --lime: #c2ce48;
    --lime-light: #d6e166;
    --ink-green: #2e9a3a;
    --grey-ink: #4a4a4a;
  }
  * { margin: 0; padding: 0; box-sizing: border-box; }
  html, body {
    width: 1200px; height: 1200px; overflow: hidden;
    background: var(--bg);
    font-family: "Jost", sans-serif;
  }
  .canvas { position: relative; width: 1200px; height: 1200px; }

  .pouch {
    position: absolute; left: 290px; top: 100px;
    width: 620px; height: 992px;
    background: var(--pouch);
    border: 12px solid var(--pouch-edge);
    border-top: none;
  }

  .identifier-band {
    position: absolute; left: -12px; right: -12px; top: 0; height: 104px;
    background: var(--band-green);
  }
  .identifier-band .claim {
    position: absolute; left: 0; right: 0; top: 22px;
    text-align: center; color: #fff;
    font-family: "Kaushan Script", cursive; font-size: 34px;
    transform: rotate(-2deg);
  }
  .tear-line {
    position: absolute; left: -12px; right: -12px; top: 108px;
    border-top: 1px dashed #777;
  }
  .tear-label {
    position: absolute; top: 112px; font-size: 8px; color: #444;
    font-family: Arial, sans-serif;
  }
  .tear-label.left { left: 40px; }
  .tear-label.right { right: 10px; }

  .zip-seal {
    position: absolute; left: 0; right: 0; top: 140px; height: 18px;
    background: linear-gradient(#f0f0f0, #fff, #ececec);
  }

  .brand {
    position: absolute; left: 0; right: 0; top: 208px;
    display: flex; justify-content: center; align-items: center; gap: 12px;
  }
  .brand-dot { width: 26px; height: 26px; border-radius: 50%; background: var(--lime); }
  .brand-name {
    font-size: 64px; font-weight: 400; color: var(--logo-green);
    letter-spacing: 2px;
  }

  .product-mark {
    position: absolute; left: 50%; top: 356px;
    width: 400px; height: 400px; margin-left: -200px;
    border-radius: 50%;
    background: radial-gradient(circle at 70% 60%, var(--lime-light), var(--lime) 70%);
  }
  .product-name {
    position: absolute; left: 0; right: 0; top: 440px;
    text-align: center; color: #fff;
    font-family: "Kaushan Script", cursive;
    font-size: 104px; line-height: 0.95;
    transform: rotate(-8deg);
  }

  .ingredients {
    position: absolute; left: 0; right: 0; top: 752px;
    text-align: center; color: var(--ink-green);
    font-size: 20px; font-weight: 500; line-height: 1.25;
    letter-spacing: 0.5px;
  }

  .badges {
    position: absolute; left: 20px; right: 20px; top: 828px;
    display: flex; justify-content: space-between;
  }
  .badge { width: 104px; text-align: center; }
  .badge svg { display: block; margin: 0 auto; }
  .badge-label {
    margin-top: 8px; font-size: 10px; color: var(--grey-ink);
    letter-spacing: 0.3px;
  }

  .net-weight {
    position: absolute; left: 0; right: 0; top: 938px;
    text-align: center; color: var(--ink-green);
    font-size: 20px; font-weight: 500; letter-spacing: 1px;
  }
</style>
</head>
<body>
<div class="canvas">
  <div class="pouch">
    <div class="identifier-band">
      <div class="claim">Danish Certified Organic</div>
    </div>
    <div class="tear-line"></div>
    <span class="tear-label left">Tear To Open</span>
    <span class="tear-label right">Tear To Open</span>
    <div class="zip-seal"></div>

    <div class="brand">
      <span class="brand-dot"></span>
      <span class="brand-name">PureLeafy</span>
    </div>

    <div class="product-mark"></div>
    <div class="product-name">Vital<br>Blendo</div>

    <p class="ingredients">MACA, MORINGA, BAOBAB, SPIRULINA,<br>CHLORELLA, WHEATGRASS</p>

    <div class="badges">
      <div class="badge">
        <svg width="70" height="70" viewBox="0 0 70 70">
          <circle cx="35" cy="35" r="31" fill="none" stroke="var(--lime)" stroke-width="7"/>
          <text x="35" y="34" text-anchor="middle" font-family="Jost, sans-serif" font-size="15" font-weight="500" fill="#333">100%</text>
          <text x="35" y="45" text-anchor="middle" font-family="Jost, sans-serif" font-size="8" font-weight="500" fill="#333">ORGANIC</text>
        </svg>
        <div class="badge-label">100% ORGANIC</div>
      </div>
      <div class="badge">
        <svg width="70" height="70" viewBox="0 0 70 70">
          <circle cx="35" cy="35" r="31" fill="none" stroke="var(--lime)" stroke-width="7"/>
          <text x="35" y="32" text-anchor="middle" font-family="Jost, sans-serif" font-size="14" font-weight="500" fill="#333">NON</text>
          <text x="35" y="47" text-anchor="middle" font-family="Jost, sans-serif" font-size="14" font-weight="500" fill="#333">GMO</text>
        </svg>
        <div class="badge-label">NON-GMO</div>
      </div>
      <div class="badge">
        <svg width="70" height="70" viewBox="0 0 70 70">
          <circle cx="35" cy="35" r="31" fill="none" stroke="var(--lime)" stroke-width="7"/>
          <circle cx="35" cy="35" r="14" fill="#555"/>
        </svg>
        <div class="badge-label">100% VEGAN</div>
      </div>
      <div class="badge">
        <svg width="70" height="70" viewBox="0 0 70 70">
          <circle cx="35" cy="35" r="31" fill="none" stroke="var(--lime)" stroke-width="7"/>
          <line x1="13" y1="13" x2="57" y2="57" stroke="var(--lime)" stroke-width="5"/>
          <rect x="32" y="20" width="6" height="30" fill="#555"/>
        </svg>
        <div class="badge-label">GULTEN FREE</div>
      </div>
      <div class="badge">
        <svg width="70" height="70" viewBox="0 0 70 70">
          <circle cx="35" cy="35" r="31" fill="none" stroke="var(--lime)" stroke-width="7"/>
          <line x1="13" y1="13" x2="57" y2="57" stroke="var(--lime)" stroke-width="5"/>
          <rect x="26" y="22" width="18" height="26" rx="6" fill="#555" transform="rotate(-40 35 35)"/>
        </svg>
        <div class="badge-label">NO PRESERVATIVE</div>
      </div>
    </div>

    <div class="net-weight">225 GM</div>
  </div>
</div>
</body>
</html>
```